Podcast Artwork

We require a 1440 x 1140px image for a new podcast launching soon. The podcast will be aimed at professionals working in the drug and alcohol treatment sector. The name of the show is The Kestrel Hour.

There is no existing creative for the show for you ti use as reference point.

Target Market(s)

Professionals who work in the drug and alcohol treatment sector.

Industry/Entity Type

Drug

Requirements
Must have
• the stated preferred dimensions given by zandle of Podcast artwork.
Should not have
• Lots of small images of drugs, that's too obvious.

```html
<!DOCTYPE html>
<html lang="en">
<head>
<meta charset="utf-8">
<title>The Kestrel Hour — Podcast Artwork</title>
<link rel="stylesheet" href="https://fonts.googleapis.com/css2?family=Jost:wght@300;400&display=swap">
<style>
  :root {
    --bg-deep: #1f1f1f;
    --bg-mid: #3a3a3a;
    --bg-light: #555555;
    --title-white: #ffffff;
  }
  html, body {
    margin: 0;
    padding: 0;
    width: 1200px;
    height: 947px;
    overflow: hidden;
    background: var(--bg-deep);
  }
  .cover {
    position: relative;
    width: 1200px;
    height: 947px;
    overflow: hidden;
  }
  .cover__backdrop {
    position: absolute;
    inset: 0;
    background:
      radial-gradient(ellipse at 25% 25%, var(--bg-light) 0%, transparent 45%),
      radial-gradient(ellipse at 85% 70%, var(--bg-mid) 0%, transparent 55%),
      linear-gradient(160deg, var(--bg-mid) 0%, var(--bg-deep) 100%);
  }
  .cover__title {
    position: absolute;
    top: 100px;
    left: 0;
    right: 0;
    margin: 0;
    text-align: center;
    font-family: "Jost", "Futura", sans-serif;
    font-weight: 300;
    font-size: 262px;
    line-height: 232px;
    letter-spacing: -2px;
    color: var(--title-white);
    text-transform: uppercase;
  }
  .cover__title-line {
    display: block;
  }
</style>
</head>
<body>
  <main class="cover">
    <div class="cover__backdrop" role="img" aria-label="Dark grey microscopic render of interconnected neurons with branching dendrites"></div>
    <h1 class="cover__title">
      <span class="cover__title-line">The</span>
      <span class="cover__title-line">Kestrel</span>
      <span class="cover__title-line">Hour</span>
    </h1>
  </main>
</body>
</html>
```